Kestrova - presentation for a remote DBA team offering data platform management

We need a website design for wordpress site called Kestrova.cz
We deliver remote database and data platform administration and development, oversee the database administrators, consult and train the personnel responsible for the database operations. The website should include several sections, home page with graphics elements supporting the name and service - remote dba work; blog section; service introduction and description, team introduction and description, download section for documents, presentations etc.

Target Market(s)

small and medium business companies requiring remote DBA service

Number of Pages Required

3 page

Font styles to use
Sans Serif

Colors

Designer to choose colors to be used in the design.

Requirements
Must have
• The website should have several sections to introduce the services, blog, team introduction, downloads

```html
<!DOCTYPE html>
<html lang="en">
<head>
<meta charset="utf-8">
<title>Kestrova.cz</title>
<link href="https://fonts.googleapis.com/css2?family=Roboto:wght@300;400;500;700&display=swap" rel="stylesheet">
<style>
:root{
  --blue:#3d6fe0;
  --blue-dark:#2d57c2;
  --ink:#1f2536;
  --text:#6b7285;
  --tint:#eef3fd;
  --tint-2:#e2eafb;
  --line:#d8e1f5;
  --white:#ffffff;
  --dark:#1a1d24;
}
*{box-sizing:border-box;margin:0;padding:0}
html,body{width:1200px;height:4108px;overflow:hidden}
body{font-family:"Roboto",sans-serif;color:var(--text);background:var(--white);position:relative;font-size:15px;line-height:1.6}
.abs{position:absolute}
.eyebrow{color:var(--blue);font-size:15px;text-align:center}
.title{color:var(--ink);font-size:38px;font-weight:500;text-align:center;line-height:1.2}
.chev{display:block;margin:8px auto 0}
.lead{text-align:center;font-size:15px;width:620px;margin:0 auto}
.btn{display:inline-block;background:var(--blue);color:#fff;font-size:13px;font-weight:500;letter-spacing:.5px;text-transform:uppercase;padding:12px 22px;border-radius:3px}
.photo{background:linear-gradient(135deg,#c9ced8,#8d95a6)}

/* header */
.site-header{top:0;left:0;width:1200px;height:96px}
.logo{left:80px;top:20px;font-size:32px;font-weight:500;color:var(--blue)}
.nav{right:90px;top:32px;display:flex;gap:38px;align-items:center;font-size:13px;font-weight:500;color:#8e98b3}
.nav .active{color:var(--blue);border-bottom:2px solid var(--blue);padding-bottom:4px}
.nav .btn{padding:10px 16px}

/* hero */
.hero{top:80px;left:0;width:1200px;height:600px}
.hero-card{left:118px;top:40px;width:860px;height:460px;border:2px solid var(--line);border-radius:60px 20px 60px 20px;background:linear-gradient(160deg,#f6f9ff,#e6eefc)}
.hero-card-inner{left:140px;top:60px;width:800px;height:410px;border-radius:50px 18px 50px 18px;background:linear-gradient(160deg,#eaf0fd,#dfe8fb)}
.hero-title{left:190px;top:190px;color:var(--blue);font-size:34px;font-weight:700;line-height:1.2}
.hero-sub{left:190px;top:240px;color:var(--ink);font-size:18px}
.hero-form{left:190px;top:300px;display:flex;gap:10px}
.hero-input{width:230px;height:42px;background:#fff;border:1px solid var(--line);border-radius:3px;font-size:12px;color:#9aa3b8;padding:12px 14px}
.hero-art{left:740px;top:10px;width:380px;height:380px;background:linear-gradient(150deg,#d3defc,#7d9bea);border-radius:24px;opacity:.85}

/* services */
.services{top:720px;left:0;width:1200px;height:460px}
.service{top:210px;width:300px;text-align:center}
.service h3{color:var(--ink);font-size:17px;font-weight:500;margin-top:14px}
.service p{font-size:14px;margin-top:6px}

/* about */
.about{top:1220px;left:0;width:1200px;height:460px;background:var(--tint)}
.tablet{left:60px;top:80px;width:500px;height:300px}
.about-text{left:632px;top:60px;width:480px}
.about-text .eyebrow,.about-text .title{text-align:left}
.about-text .title{font-size:36px;white-space:nowrap}
.about-text p{font-size:14px;margin-top:18px;width:380px}
.about-text p.eyebrow{margin-top:0;font-size:15px}

/* team */
.team{top:1730px;left:0;width:1200px;height:590px}
.member{top:220px;width:240px;height:320px;background:#fff;box-shadow:0 6px 20px rgba(40,60,120,.12)}
.member .photo{height:240px;position:relative}
.member .cap{position:absolute;left:0;bottom:0;width:100%;height:60px;background:rgba(255,255,255,.85);text-align:center;padding-top:8px}
.member .cap b{display:block;color:var(--ink);font-size:15px;font-weight:500}
.member .cap span{font-size:12px}
.socials{display:flex;gap:8px;padding:18px 0 0 60px}
.dot{width:26px;height:26px;border-radius:50%;border:1px solid var(--line);background:#fff}
.dot.fill{background:var(--blue);border-color:var(--blue)}

/* posts */
.posts{top:2320px;left:0;width:1200px;height:660px;background:var(--tint)}
.post{top:180px;width:310px;height:450px;background:#fff;box-shadow:0 6px 20px rgba(40,60,120,.1)}
.post.dark{background:#2a2d34}
.post .photo{margin:20px;height:180px;background:linear-gradient(135deg,#2b3b5a,#8aa0c8)}
.post .meta{margin:0 22px;font-size:12px;border-top:2px solid var(--line);padding-top:10px}
.post h4{margin:8px 22px 0;color:var(--blue);font-size:15px;font-weight:500}
.post p{margin:14px 22px 0;font-size:13px}
.post.dark .meta,.post.dark p{color:#c7ccd8}
.post.dark h4{color:#fff}
.post .plus{position:absolute;left:22px;bottom:-20px;width:40px;height:40px;border-radius:50%;background:#fff;border:1px solid var(--line)}

/* download band */
.band{top:2992px;left:0;width:1200px;height:200px;background:linear-gradient(90deg,#121419,#2b2f38 60%,#1a1d22)}
.band p{position:absolute;left:72px;top:52px;width:480px;color:#e8eaf0;font-size:15px}
.band .btn{position:absolute;right:90px;top:74px}

/* contact */
.contact{top:3230px;left:0;width:1200px;height:540px}
.form{left:400px;top:220px;width:400px}
.field{height:42px;border:1px solid var(--line);border-radius:3px;font-size:13px;color:#9aa3b8;padding:11px 14px;margin-bottom:14px}
.field.active{border-color:var(--blue)}
.field.msg{height:76px}

/* footer */
.site-footer{top:3780px;left:0;width:1200px;height:328px;background:var(--blue);color:#e6edff}
.col{top:42px;font-size:14px}
.col h5{color:#fff;font-size:16px;font-weight:500;margin-bottom:14px}
.col li{list-style:none;margin-bottom:6px;padding-left:16px;position:relative}
.col li::before{content:"";position:absolute;left:0;top:9px;width:6px;height:6px;border-radius:50%;background:#fff}
.contact-row{display:flex;gap:12px;margin-bottom:16px;align-items:flex-start}
.foot-brand{left:900px;top:34px;width:240px;text-align:center}
.foot-brand h5{font-size:26px;font-weight:500;color:#fff}
.foot-brand p{font-size:14px;margin-top:10px}
.foot-brand .socials{justify-content:center;padding:14px 0 0}
.foot-brand .dot{background:transparent;border-color:#fff}
.copy{left:0;bottom:0;width:1200px;height:56px;border-top:1px solid rgba(255,255,255,.3);text-align:center;line-height:56px;font-size:13px;color:#fff}
</style>
</head>
<body>

<header class="site-header abs">
  <div class="logo abs">Kestrova.cz</div>
  <nav class="nav abs">
    <span class="active">HOME</span><span>ABOUT US</span><span>SERVICES</span><span>BLOG</span><span>CONTACT US</span>
    <span class="btn">Get a Quote</span>
  </nav>
</header>

<section class="hero abs">
  <div class="hero-card abs"></div>
  <div class="hero-card-inner abs"></div>
  <div class="hero-art abs" role="img" aria-label="Isometric illustration of a data server with people working on it"></div>
  <h1 class="hero-title abs">KESTROVA</h1>
  <p class="hero-sub abs">Lorem Ipsum is simply dummy text of typesetting industry.</p>
  <div class="hero-form abs"><div class="hero-input">Enter your e-mail address</div><span class="btn">Get Started</span></div>
</section>

<section class="services abs">
  <p class="eyebrow">Our Services</p>
  <h2 class="title">What We Can Do</h2>
  <svg class="chev" width="22" height="12" viewBox="0 0 22 12"><path d="M2 2l9 8 9-8" fill="none" stroke="#3d6fe0" stroke-width="3"/></svg>
  <p class="lead" style="margin-top:22px">Lorem Ipsum is simply dummy text of the printing and typesetting industry. Lorem Ipsum has been the industry's standard dummy text ever since the 1500s.</p>
  <div class="service abs" style="left:90px">
    <svg width="70" height="70" viewBox="0 0 70 70"><path d="M12 35a23 23 0 0 1 40-15" fill="none" stroke="#3d6fe0" stroke-width="4"/><path d="M58 35a23 23 0 0 1-40 15" fill="none" stroke="#3d6fe0" stroke-width="4"/><rect x="27" y="28" width="16" height="14" rx="2" fill="#3d6fe0"/></svg>
    <h3>Remote database</h3>
    <p>Lorem Ipsum is simply dummy text of the printing and typesetting industry.</p>
  </div>
  <div class="service abs" style="left:450px">
    <svg width="70" height="70" viewBox="0 0 70 70"><circle cx="35" cy="35" r="30" fill="#dfe8fb"/><circle cx="35" cy="35" r="22" fill="#3d6fe0"/><rect x="27" y="27" width="16" height="16" rx="2" fill="#fff"/></svg>
    <h3>Data platform administration</h3>
    <p>Lorem Ipsum is simply dummy text of the printing and typesetting industry.</p>
  </div>
  <div class="service abs" style="left:810px">
    <svg width="70" height="70" viewBox="0 0 70 70"><path d="M14 40a22 22 0 0 1 36-24" fill="none" stroke="#3d6fe0" stroke-width="4"/><path d="M56 30a22 22 0 0 1-36 24" fill="none" stroke="#3d6fe0" stroke-width="4"/><circle cx="35" cy="35" r="6" fill="#3d6fe0"/></svg>
    <h3>Development</h3>
    <p>Lorem Ipsum is simply dummy text of the printing and typesetting industry.</p>
  </div>
</section>

<section class="about abs">
  <div class="tablet abs" role="img" aria-label="Tablet showing the Kestrova website with a data illustration" style="background:linear-gradient(135deg,#2a2e38,#4a5060);border-radius:16px;padding:16px"><div style="width:100%;height:100%;background:linear-gradient(135deg,#f4f7ff,#d6e2fb)"></div></div>
  <div class="about-text abs">
    <p class="eyebrow">About Us</p>
    <h2 class="title">Welcome To Kestrova.cz</h2>
    <svg width="22" height="12" viewBox="0 0 22 12" style="margin-top:8px"><path d="M2 2l9 8 9-8" fill="none" stroke="#3d6fe0" stroke-width="3"/></svg>
    <p>Lorem Ipsum is simply dummy text of the printing and typesetting industry. Lorem Ipsum has been the industry's standard dummy.</p>
    <p>1500s, when an unknown printer took a galley of type and scrambled it to make a type specimen book. It has also the leap into electronic typesetting, remaining essentially unchanged.</p>
    <span class="btn" style="margin-top:26px">Learn More</span>
  </div>
</section>

<section class="team abs">
  <p class="eyebrow">Meet The Team</p>
  <h2 class="title">Our Team</h2>
  <svg class="chev" width="22" height="12" viewBox="0 0 22 12"><path d="M2 2l9 8 9-8" fill="none" stroke="#3d6fe0" stroke-width="3"/></svg>
  <p class="lead" style="margin-top:22px">Lorem Ipsum is simply dummy text of the printing and typesetting industry. Lorem Ipsum has been the industry's standard dummy text ever since the 1500s.</p>
  <div class="member abs" style="left:72px"><div class="photo" role="img" aria-label="Portrait of a team member"><div class="cap"><b>Member Name</b><span>Position</span></div></div><div class="socials"><span class="dot fill"></span><span class="dot"></span><span class="dot"></span></div></div>
  <div class="member abs" style="left:344px"><div class="photo" role="img" aria-label="Portrait of a team member"><div class="cap"><b>Member Name</b><span>Position</span></div></div><div class="socials"><span class="dot fill"></span><span class="dot"></span><span class="dot"></span></div></div>
  <div class="member abs" style="left:616px"><div class="photo" role="img" aria-label="Portrait of a team member"><div class="cap"><b>Member Name</b><span>Position</span></div></div><div class="socials"><span class="dot fill"></span><span class="dot"></span><span class="dot"></span></div></div>
  <div class="member abs" style="left:888px"><div class="photo" role="img" aria-label="Portrait of a team member"><div class="cap"><b>Member Name</b><span>Position</span></div></div><div class="socials"><span class="dot fill"></span><span class="dot"></span><span class="dot"></span></div></div>
</section>

<section class="posts abs">
  <p class="eyebrow" style="margin-top:40px">Recent News</p>
  <h2 class="title">Latest Post</h2>
  <svg class="chev" width="22" height="12" viewBox="0 0 22 12"><path d="M2 2l9 8 9-8" fill="none" stroke="#3d6fe0" stroke-width="3"/></svg>
  <article class="post abs" style="left:100px"><div class="photo" role="img" aria-label="Photo of hands on a laptop with data graphics"></div><p class="meta">01, JAN 2020</p><h4>Lorem Ipsum is simply dummy</h4><p>Lorem Ipsum is simply dummy text of the printing and typesetting industry.</p><span class="plus"></span></article>
  <article class="post dark abs" style="left:452px"><div class="photo" role="img" aria-label="Photo of a team meeting around a table"></div><p class="meta">01, JAN 2020</p><h4>Lorem Ipsum is simply dummy</h4><p>Lorem Ipsum is simply dummy text of the printing and typesetting industry.</p><span class="btn" style="margin:26px 22px 0">Read More</span></article>
  <article class="post abs" style="left:792px"><div class="photo" role="img" aria-label="Photo of a person working at a laptop"></div><p class="meta">01, JAN 2020</p><h4>Lorem Ipsum is simply dummy</h4><p>Lorem Ipsum is simply dummy text of the printing and typesetting industry.</p><span class="plus"></span></article>
</section>

<section class="band abs" role="img" aria-label="Dark photo of a desk with laptops as background">
  <p>Lorem Ipsum is simply dummy text of the printing and typesetting industry. Lorem Ipsum has been the industry's standard dummy text took a galley of type and scrambled it to make a type specimen book.</p>
  <span class="btn">Download Presentation</span>
</section>

<section class="contact abs">
  <p class="eyebrow" style="margin-top:30px">Contact Us</p>
  <h2 class="title">Contact Form</h2>
  <svg class="chev" width="22" height="12" viewBox="0 0 22 12"><path d="M2 2l9 8 9-8" fill="none" stroke="#3d6fe0" stroke-width="3"/></svg>
  <p class="lead" style="margin-top:22px">Lorem Ipsum is simply dummy text of the printing and typesetting industry. Lorem Ipsum has been the industry's standard dummy text ever since the 1500s.</p>
  <form class="form abs">
    <div class="field active">Name*</div>
    <div class="field">E-mail*</div>
    <div class="field">Phone*</div>
    <div class="field msg">Message</div>
    <span class="btn">Submit</span>
  </form>
</section>

<footer class="site-footer abs">
  <div class="col abs" style="left:80px"><h5>Navigation</h5><ul><li>Home</li><li>About Us</li><li>Services</li><li>Blog</li><li>Contact Us</li></ul></div>
  <div class="col abs" style="left:345px;width:230px"><h5>Get In Touch</h5>
    <div class="contact-row"><svg width="16" height="20" viewBox="0 0 16 20"><path d="M8 1a7 7 0 0 1 7 7c0 5-7 11-7 11S1 13 1 8a7 7 0 0 1 7-7z" fill="#fff"/><circle cx="8" cy="8" r="2.5" fill="#3d6fe0"/></svg><span>123, Address, State Name, City Name, Zipcode</span></div>
    <div class="contact-row"><svg width="16" height="16" viewBox="0 0 16 16"><path d="M3 1l3 3-2 2c1 2 3 4 5 5l2-2 3 3-2 3C6 15 1 10 1 3z" fill="#fff"/></svg><span>555 014 2288</span></div>
    <div class="contact-row"><svg width="16" height="12" viewBox="0 0 16 12"><rect width="16" height="12" rx="1" fill="#fff"/><path d="M1 1l7 6 7-6" fill="none" stroke="#3d6fe0" stroke-width="1.5"/></svg><span>info@kestrova.cz</span></div>
  </div>
  <div class="col abs" style="left:620px"><h5>Services</h5><ul><li>Remote database</li><li>Data platform administration</li><li>Development</li></ul></div>
  <div class="foot-brand abs"><h5>Kestrova.cz</h5><p>Lorem Ipsum is simply dummy text of the printing and typesetting industry. Lorem Ipsum standard dummy text ever since.</p><div class="socials"><span class="dot"></span><span class="dot"></span><span class="dot"></span><span class="dot"></span></div></div>
  <div class="copy abs">© KESTROVA.CZ - 2018, All Rights Reserved.</div>
</footer>

</body>
</html>
```